Brightfen Business Card Redesign & Logo Update

We need to update our business cards to something more modern and fresh. Brightfen can provide the current color schemes and old design examples, but welcome creativity in helping us with this redesign. PLEASE NOTE that we no longer utilize the "tree" and/or "leaf" imagery in our branding. If able would apprecaite an update on the quality of our "words only" logo in Ai. / PNG formats too.

Target Market(s)

Investors, landowners, corporate partners, contractors

Industry/Entity Type

Environmental Restoration & Conservation

Contact Information for Business Card

Logo, persons name, title, mailing address, phone and email, website url

Font styles to use
Other font styles liked:
• Merriweather

Requirements
Nice to have
• Logo, persons name, title, mailing address, phone and email, website url, but open to ideams
Should not have
• No all back backgrounds

```html
<!DOCTYPE html>
<html lang="en">
<head>
<meta charset="utf-8">
<title>Brightfen Business Card</title>
<link rel="stylesheet" href="https://fonts.googleapis.com/css2?family=Montserrat:wght@400;500;700;800&display=swap">
<style>
  :root {
    --green: #167a3f;
    --orange: #ee7d1f;
    --ink: #1d1d1d;
    --paper: #ffffff;
    --backdrop: #e9ebe8;
  }
  * { margin: 0; padding: 0; box-sizing: border-box; }
  html, body { width: 1200px; height: 900px; overflow: hidden; }
  body {
    background: var(--backdrop);
    font-family: "Montserrat", Arial, sans-serif;
    position: relative;
  }
  .card {
    position: absolute;
    left: 250px;
    width: 700px;
    height: 400px;
    border-radius: 28px;
    overflow: hidden;
    box-shadow: 0 10px 30px rgba(0,0,0,0.18);
  }
  .card-front { top: 40px; background: var(--paper); }
  .card-back { top: 460px; background: var(--green); }

  .swoosh { position: absolute; inset: 0; width: 700px; height: 400px; }

  .brand { position: absolute; }
  .brand-name {
    font-weight: 800;
    letter-spacing: 1px;
    line-height: 1;
    white-space: nowrap;
  }
  .brand-tagline {
    font-weight: 500;
    text-transform: uppercase;
    white-space: nowrap;
    display: flex;
    align-items: center;
  }
  .brand-tagline::before,
  .brand-tagline::after {
    content: "";
    display: block;
    height: 2px;
    background: currentColor;
  }
  .card-front .brand { left: 40px; top: 125px; }
  .card-front .brand-name { font-size: 44px; color: var(--green); }
  .card-front .brand-tagline { font-size: 10px; color: var(--green); margin-top: 10px; letter-spacing: 1.5px; gap: 8px; }
  .card-front .brand-tagline::before { width: 24px; background: var(--orange); }
  .card-front .brand-tagline::after { width: 24px; background: var(--orange); }

  .divider {
    position: absolute;
    left: 370px; top: 80px;
    width: 1.5px; height: 230px;
    background: var(--green);
  }

  .contact { position: absolute; left: 395px; top: 90px; color: var(--ink); }
  .person-name { font-size: 25px; font-weight: 800; letter-spacing: 0.5px; line-height: 1.1; white-space: nowrap; }
  .person-name .first { color: var(--green); }
  .person-name .last { color: var(--orange); }
  .person-title { font-size: 15px; margin-bottom: 14px; }
  .address { font-size: 15px; line-height: 1.45; margin-bottom: 12px; white-space: nowrap; }
  .contact-list { list-style: none; font-size: 15px; line-height: 1.6; }
  .contact-list li { display: flex; align-items: center; gap: 8px; white-space: nowrap; }
  .contact-list svg { width: 13px; height: 13px; flex: none; }

  .card-back .brand {
    left: 0; right: 0; top: 150px;
    text-align: center; color: var(--paper);
    display: flex; flex-direction: column; align-items: center;
  }
  .card-back .brand-name { font-size: 80px; letter-spacing: 3px; }
  .card-back .brand-tagline { font-size: 16px; margin-top: 16px; letter-spacing: 2.5px; gap: 14px; }
  .card-back .brand-tagline::before,
  .card-back .brand-tagline::after { width: 40px; }
</style>
</head>
<body>

  <section class="card card-front">
    <svg class="swoosh" viewBox="0 0 700 400" aria-hidden="true">
      <path d="M0,190 Q170,350 520,400 L0,400 Z" fill="var(--green)"/>
      <path d="M200,316 Q380,382 565,400 L520,400 Q350,378 200,316 Z" fill="var(--orange)"/>
    </svg>

    <div class="brand">
      <div class="brand-name">BRIGHTFEN</div>
      <div class="brand-tagline">Environmental Credit Company</div>
    </div>

    <div class="divider"></div>

    <div class="contact">
      <div class="person-name"><span class="first">NORA</span> <span class="last">WHITLEY</span></div>
      <div class="person-title">CEO/Founder</div>
      <div class="address">48 Meadow Lane<br>Fenwick Vale, ON 20731</div>
      <ul class="contact-list">
        <li>
          <svg viewBox="0 0 16 16"><circle cx="8" cy="8" r="8" fill="var(--orange)"/><path d="M5 4.5l1.6-.4 1 2.2-1 .8a5 5 0 0 0 2.3 2.3l.8-1 2.2 1-.4 1.6C8.6 11.3 4.7 7.4 5 4.5z" fill="#fff"/></svg>
          (555) 218 4630
        </li>
        <li>
          <svg viewBox="0 0 16 16"><rect x="1" y="3" width="14" height="10" rx="1" fill="var(--orange)"/><path d="M1.5 3.5L8 9l6.5-5.5" stroke="#fff" stroke-width="1.3" fill="none"/></svg>
          nora@brightfen.com
        </li>
        <li>
          <svg viewBox="0 0 16 16"><circle cx="8" cy="8" r="7.5" fill="var(--orange)"/><path d="M8 1v14M1 8h14M8 1c-3 3-3 11 0 14M8 1c3 3 3 11 0 14" stroke="#fff" stroke-width="1" fill="none"/></svg>
          www.brightfen.com
        </li>
      </ul>
    </div>
  </section>

  <section class="card card-back">
    <div class="brand">
      <div class="brand-name">BRIGHTFEN</div>
      <div class="brand-tagline">Environmental Credit Company</div>
    </div>
  </section>

</body>
</html>
```